Meadowlight Soaps Business Card

The new business card design will incorporate my new logo components designed by one of your designers. Meadowlight Soaps creates high quality soaps and bath products. They would be suited for a Spa, Bed and Breakfast, Boutique environment. The look should be a white background.
Classy, soft and using the colour palet of the logo. The card will be two sided.

Reason: Need more time to make some changes and decide.

Target Market(s)

Looking to appeal to an upper end market. Spas, boutiques, independent gift stores, bridal salons, bed and breakfast, etc. I want the card to impart a sense of elegance, tranquility and Meadowlight. But also quality and value.

Industry/Entity Type

Business

Font styles to use
Sans Serif
Script

Requirements
Must have
• My logo on the front. But also on the back but faded out to allow written notes on the back.
On the front : Carol Pritchett
Owner/Creator
48 Fenwick Rd
Guelph, Ont N4K 2P9
519.402.6183
Creating Quality Handcrafted Soaps And Bath Products
Custom and Wholesale Orders Welcome
Www.meadowlightsoaps.ca
Www.facebook.com / MeadowlightSoapandBath
info@meadowlightsoaps.ca

```html
<!DOCTYPE html>
<html lang="en">
<head>
<meta charset="utf-8">
<title>Meadowlight Soaps Business Card</title>
<link rel="stylesheet" href="https://fonts.googleapis.com/css2?family=Lato:wght@400;700&family=Parisienne&display=swap">
<style>
  :root {
    --backdrop: #3b3b3c;
    --paper: #ffffff;
    --sage: #88b4aa;
    --sage-deep: #7aa79c;
    --sand: #e8d6c6;
    --sand-text: #f1dccb;
    --faint-sage: #e3ece9;
    --ink-light: #ffffff;
  }
  * { box-sizing: border-box; margin: 0; padding: 0; }
  html, body { width: 1200px; height: 1000px; overflow: hidden; }
  body { background: var(--backdrop); position: relative; font-family: "Lato", sans-serif; }

  .card {
    position: absolute;
    background: var(--paper);
    overflow: hidden;
    box-shadow: 0 3px 6px rgba(0,0,0,0.35);
  }
  .card--front { left: 312px; top: 126px; width: 500px; height: 292px; }
  .card--back  { left: 61px;  top: 546px; width: 500px; height: 292px; }
  .card--notes { left: 642px; top: 544px; width: 504px; height: 294px; }

  .front-curves { position: absolute; inset: 0; }

  .brand-mark {
    position: absolute; left: 18px; top: 48px; width: 200px; height: 190px;
    display: flex; flex-direction: column; align-items: center; justify-content: flex-end;
  }
  .brand-mark__dot {
    width: 96px; height: 96px; border-radius: 50%;
    background: var(--sage); opacity: 0.35; margin-bottom: 18px;
  }
  .brand-mark__name {
    font-family: "Lato", sans-serif; font-weight: 400; color: var(--sage-deep);
    font-size: 19px; letter-spacing: 1px; text-align: center; line-height: 1.15;
  }

  .contact {
    position: absolute; right: 28px; top: 0; width: 240px; text-align: right; color: var(--ink-light);
  }
  .contact__tagline {
    position: absolute; right: 2px; top: 27px; width: 240px;
    color: var(--sand-text); font-size: 11.5px; line-height: 19px;
  }
  .contact__name {
    position: absolute; right: 0; top: 82px; white-space: nowrap;
    font-family: "Parisienne", cursive; font-size: 25px; color: var(--sand-text);
  }
  .contact__role { position: absolute; right: 0; top: 116px; font-size: 13px; }
  .contact__address { position: absolute; right: 0; top: 156px; font-size: 11px; line-height: 17px; }
  .contact__links { position: absolute; right: 0; top: 210px; list-style: none; font-size: 11px; }
  .contact__links li {
    display: flex; justify-content: flex-end; align-items: center; gap: 7px; height: 19.5px; white-space: nowrap;
  }
  .icon { width: 12px; height: 12px; display: block; }

  .faded-mark {
    position: absolute; left: 50%; top: 30px; transform: translateX(-50%);
    display: flex; flex-direction: column; align-items: center;
  }
  .faded-mark__dot {
    width: 190px; height: 190px; border-radius: 50%; background: var(--faint-sage);
  }
  .faded-mark__name {
    margin-top: 14px; font-family: "Lato", sans-serif; font-weight: 400;
    font-size: 22px; letter-spacing: 1px; color: var(--faint-sage); white-space: nowrap;
  }
  .notes-label {
    position: absolute; left: 26px; top: 28px;
    font-family: "Parisienne", cursive; font-size: 24px; color: var(--sage-deep);
  }
</style>
</head>
<body>

  <section class="card card--front" aria-label="Business card front">
    <svg class="front-curves" viewBox="0 0 500 292" width="500" height="292" aria-hidden="true">
      <path d="M218,0 C305,70 290,225 188,292 L500,292 L500,0 Z" fill="var(--sand)"/>
      <path d="M218,0 C292,62 302,220 232,292 L500,292 L500,0 Z" fill="var(--sage)"/>
    </svg>

    <div class="brand-mark">
      <span class="brand-mark__dot"></span>
      <span class="brand-mark__name">Meadowlight Soaps</span>
    </div>

    <div class="contact">
      <p class="contact__tagline">Creating Quality Handcrafted<br>Soaps And Bath Products</p>
      <p class="contact__name">Carol Pritchett</p>
      <p class="contact__role">Owner/Creator</p>
      <p class="contact__address">48 Fenwick Rd<br>Guelph,Ont N4K 2P9</p>
      <ul class="contact__links">
        <li>519.402.6183
          <svg class="icon" viewBox="0 0 12 12" aria-hidden="true"><path d="M2.5 1 L4.5 1 L5.2 3.6 L4 4.6 C4.6 6 6 7.4 7.4 8 L8.4 6.8 L11 7.5 L11 9.5 C11 10.3 10.3 11 9.5 11 C5 11 1 7 1 2.5 C1 1.7 1.7 1 2.5 1 Z" fill="none" stroke="var(--sand)" stroke-width="1.1"/></svg>
        </li>
        <li>www.meadowlightsoaps.ca
          <svg class="icon" viewBox="0 0 12 12" aria-hidden="true"><g fill="none" stroke="var(--sand)" stroke-width="1"><circle cx="6" cy="6" r="5"/><ellipse cx="6" cy="6" rx="2.2" ry="5"/><path d="M1 6 H11"/></g></svg>
        </li>
        <li>MeadowlightSoapandBath
          <svg class="icon" viewBox="0 0 12 12" aria-hidden="true"><circle cx="6" cy="6" r="5" fill="var(--sand)"/></svg>
        </li>
      </ul>
    </div>
  </section>

  <section class="card card--back" aria-label="Business card back">
    <div class="faded-mark">
      <span class="faded-mark__dot"></span>
      <span class="faded-mark__name">Meadowlight Soaps</span>
    </div>
  </section>

  <section class="card card--notes" aria-label="Business card back with notes">
    <p class="notes-label">Notes:</p>
    <div class="faded-mark">
      <span class="faded-mark__dot"></span>
      <span class="faded-mark__name">Meadowlight Soaps</span>
    </div>
  </section>

</body>
</html>
```